BrindleStaffing Business Card Design

We are a staffing company finding positions for dedicated nurses and physicians.

Target Market(s)

Business Professionals

Industry/Entity Type

Staffing

Contact Information for Business Card

Gordon Pratley
Chairman
417 39th Avenue South
SAINT PETERSBURG FL 33712
813-555-4172 Mobile
813-555-8036 Fax
gpratley@brindlestaffing.com
www.brindlestaffing.com

Font styles to use
Sans Serif

Colors
fbee3e
f04a50
f37122

Requirements
Must have
• Logo Attached, see colors below. We'd like to see Yellow, Orange and Red.

```html
<!DOCTYPE html>
<html lang="en">
<head>
<meta charset="utf-8">
<title>BrindleStaffing Business Card</title>
<link rel="stylesheet" href="https://fonts.googleapis.com/css2?family=Roboto:wght@400;500;700&display=swap">
<style>
  :root {
    --stage: #e9ebee;
    --brand-orange: #f37122;
    --brand-red: #f04a50;
    --brand-yellow: #fbee3e;
    --paper: #ffffff;
    --ink-light: #ffffff;
  }
  * { margin: 0; padding: 0; box-sizing: border-box; }
  html, body {
    width: 1200px; height: 768px; overflow: hidden;
    background: var(--stage);
    font-family: "Roboto", Arial, sans-serif;
  }
  .stage {
    position: relative; width: 1200px; height: 768px;
    display: flex; align-items: center; justify-content: center; gap: 50px;
  }
  .card {
    position: relative; width: 540px; height: 308px;
    border-radius: 18px; overflow: hidden;
    box-shadow: 0 10px 28px rgba(0,0,0,0.18);
  }
  /* Back side */
  .card-back { background: var(--brand-orange); }
  .card-back .dot-field {
    position: absolute; inset: 0;
    background: linear-gradient(160deg, var(--brand-orange) 0%, #f25e3a 60%, var(--brand-red) 100%);
  }
  .card-back .wordmark {
    position: absolute; left: 0; right: 0; top: 118px;
    text-align: center; color: var(--ink-light);
    font-weight: 700; font-size: 46px; letter-spacing: -0.5px;
  }
  .card-back .accent-bar {
    position: absolute; left: 50%; top: 182px; width: 60px; height: 4px;
    margin-left: -30px; border-radius: 2px; background: var(--brand-yellow);
  }
  .card-back .website {
    position: absolute; left: 0; right: 0; bottom: 32px;
    text-align: center; color: var(--ink-light);
    font-size: 13px; letter-spacing: 5px;
  }
  /* Front side */
  .card-front { background: linear-gradient(160deg, var(--brand-orange), #f25e3a); }
  .card-front .sweep { position: absolute; inset: 0; }
  .contact { position: absolute; left: 30px; top: 24px; color: var(--ink-light); }
  .contact .name { font-weight: 700; font-size: 22px; line-height: 1.05; }
  .contact .title { font-size: 14px; margin-bottom: 12px; }
  .contact .address { font-size: 13px; line-height: 1.3; margin-bottom: 6px; }
  .contact .line {
    display: flex; align-items: center; gap: 8px;
    font-size: 13px; line-height: 1.35;
  }
  .contact .line svg { width: 12px; height: 12px; flex: none; }
  .card-front .wordmark {
    position: absolute; right: 34px; bottom: 46px;
    color: var(--brand-red); font-weight: 700; font-size: 34px; letter-spacing: -0.3px;
  }
</style>
</head>
<body>
<main class="stage">
  <section class="card card-back">
    <div class="dot-field" role="img" aria-label="Soft pattern of light orange dots across the card"></div>
    <div class="wordmark">BrindleStaffing</div>
    <div class="accent-bar"></div>
    <div class="website">www.brindlestaffing.com</div>
  </section>

  <section class="card card-front">
    <svg class="sweep" viewBox="0 0 540 308" aria-hidden="true">
      <path d="M160,308 C235,160 380,68 540,62 L540,308 Z" fill="var(--paper)"/>
      <path d="M148,308 C222,150 370,56 522,52" fill="none" stroke="var(--brand-yellow)" stroke-width="3"/>
    </svg>
    <div class="contact">
      <div class="name">Gordon Pratley</div>
      <div class="title">Chairman</div>
      <div class="address">417 39th Avenue South<br>SAINT PETERSBURG FL 33712</div>
      <div class="line">
        <svg viewBox="0 0 12 12"><rect x="2.5" y="0.5" width="7" height="11" rx="1.2" fill="none" stroke="#fff" stroke-width="1.2"/><rect x="5" y="9" width="2" height="1" fill="#fff"/></svg>
        813-555-4172
      </div>
      <div class="line">
        <svg viewBox="0 0 12 12"><rect x="3" y="0.5" width="6" height="4" fill="#fff"/><rect x="0.5" y="4" width="11" height="5" rx="1" fill="#fff"/><rect x="3" y="8" width="6" height="3.5" fill="#fff" stroke="var(--brand-orange)" stroke-width="0.8"/></svg>
        813-555-8036
      </div>
      <div class="line">
        <svg viewBox="0 0 12 12"><rect x="0.5" y="2" width="11" height="8" fill="none" stroke="#fff" stroke-width="1.2"/><path d="M0.5,2 L6,7 L11.5,2" fill="none" stroke="#fff" stroke-width="1.2"/></svg>
        gpratley@brindlestaffing.com
      </div>
      <div class="line">
        <svg viewBox="0 0 12 12"><circle cx="6" cy="6" r="5.3" fill="none" stroke="#fff" stroke-width="1.2"/><path d="M0.7,6 H11.3 M6,0.7 C3,3.5 3,8.5 6,11.3 M6,0.7 C9,3.5 9,8.5 6,11.3" fill="none" stroke="#fff" stroke-width="1"/></svg>
        www.brindlestaffing.com
      </div>
    </div>
    <div class="wordmark">BrindleStaffing</div>
  </section>
</main>
</body>
</html>
```